Simple Logo Design for Semi-Clear Plastic Frosted Card stock

Create a business card on frosted plastic. compliment existing logo elements with a tree trunk, roots, or seed at the lower half and the full logo both on the front.

Contact information will go on a solid portion of the back of this design since this card stock is semi-transparent.

It is important to consider this plastic card stock medium in your design. I found helpful tips and guides listed at vellaprint-sample.net: be careful to understand ink printed on plastic cards cannot have too much of a consistent print area or risks peeling and fine lines can easily scratch off.
Updates

2" x 3.5" 20PT Clear Plastic Business cards with Round corners Please get info or templates here: https://www.vellaprint-sample.net/product-detail/2-x-35-20pt-clear-plastic-business-cards-with-round-corners

Target Market(s)

Not for profit- religion

Industry/Entity Type

Business

Must include complementary elements to the existing logo

Font styles to use
Decorative

Colors
000000

Requirements
Must have
• Elements of community, nature and oneness. Such as: seed, roots, tree trunk, etc.
• Three lines of space on the back for Name, Title, Phone Number.
Nice to have
• I like a light use of decorative elements
Should not have
• No eyes, from faces or animals.

```html
<!DOCTYPE html>
<html lang="en">
<head>
<meta charset="utf-8">
<title>Kindred Grove – Business Card</title>
<link href="https://fonts.googleapis.com/css2?family=Open+Sans:wght@400;600&display=swap" rel="stylesheet">
<style>
  :root {
    --page: #e9e6e1;
    --card-black: #0c0c0c;
    --teal: #23706e;
    --green: #4aa046;
    --leaf: #5cb548;
    --grey: #5f6466;
    --white: #ffffff;
  }
  * { box-sizing: border-box; margin: 0; padding: 0; }
  html, body {
    width: 1200px; height: 900px; overflow: hidden;
    background: var(--page);
    font-family: "Open Sans", Arial, sans-serif;
  }
  .canvas { position: relative; width: 1200px; height: 900px; }
  .card {
    position: absolute; width: 560px; height: 320px;
    background: var(--card-black);
    border-radius: 16px; overflow: hidden;
    box-shadow: 0 10px 28px rgba(0,0,0,.25);
  }
  .card--front { left: 120px; top: 100px; }
  .card--back { left: 520px; top: 470px; }

  .brand-lockup {
    position: absolute; left: 0; right: 0; top: 112px;
    display: flex; flex-direction: column; align-items: center;
  }
  .brand-row { display: flex; align-items: center; gap: 12px; }
  .brand-mark { width: 26px; height: 26px; border-radius: 50%; background: var(--teal); }
  .brand-name {
    font-size: 34px; font-weight: 400; letter-spacing: 3px;
    color: var(--teal); text-transform: uppercase;
  }
  .brand-tagline {
    margin-top: 6px; font-size: 10px; letter-spacing: 2.4px;
    color: var(--grey); text-transform: uppercase;
  }

  .back-wave { position: absolute; inset: 0; }
  .back-brand {
    position: absolute; right: 40px; top: 46px;
    display: flex; align-items: center; gap: 8px;
  }
  .back-brand .brand-mark { width: 16px; height: 16px; }
  .back-brand .brand-name { font-size: 18px; letter-spacing: 1.5px; }

  .contact { position: absolute; left: 62px; top: 140px; }
  .contact-name { font-size: 22px; color: var(--green); line-height: 1.1; }
  .contact-title { font-size: 14px; color: var(--white); margin-top: 2px; }
  .contact-phone {
    display: flex; align-items: center; gap: 8px;
    margin-top: 30px; font-size: 15px; color: var(--white);
  }
  .phone-icon { width: 12px; height: 12px; }
</style>
</head>
<body>
<main class="canvas">

  <section class="card card--front" aria-label="Card front">
    <div class="brand-lockup">
      <div class="brand-row">
        <span class="brand-mark"></span>
        <span class="brand-name">Kindred Grove</span>
      </div>
      <p class="brand-tagline">Learning, Fellowship &amp; Calm</p>
    </div>
  </section>

  <section class="card card--back" aria-label="Card back">
    <svg class="back-wave" viewBox="0 0 560 320" preserveAspectRatio="none" aria-hidden="true">
      <path d="M0,262 C150,280 300,240 450,150 C330,250 170,292 0,282 Z" fill="var(--green)"/>
      <path d="M0,292 C170,300 360,230 560,110 L560,320 L0,320 Z" fill="var(--teal)"/>
      <path d="M0,288 C170,296 360,226 560,106" fill="none" stroke="var(--card-black)" stroke-width="4"/>
    </svg>

    <div class="back-brand">
      <span class="brand-mark"></span>
      <span class="brand-name">Kindred Grove</span>
    </div>

    <div class="contact">
      <p class="contact-name">Daniel Reyes</p>
      <p class="contact-title">Managing Director</p>
      <p class="contact-phone">
        <svg class="phone-icon" viewBox="0 0 24 24" aria-hidden="true">
          <path fill="var(--green)" d="M6.6 10.8c1.4 2.8 3.8 5.1 6.6 6.6l2.2-2.2c.3-.3.7-.4 1-.2 1.1.4 2.3.6 3.6.6.6 0 1 .4 1 1V20c0 .6-.4 1-1 1C10.6 21 3 13.4 3 4c0-.6.4-1 1-1h3.5c.6 0 1 .4 1 1 0 1.3.2 2.5.6 3.6.1.3 0 .7-.2 1z"/>
        </svg>
        (055)-318-2046
      </p>
    </div>
  </section>

</main>
</body>
</html>
```